brightquokka.net we need a webpage designed for our new product

We need a webpage designed for our new range of products from our new brand. We have had a logo designed on sketchharbor (see attached) and we want to keep to this theme. Our first product is a range of affordable app controlled LED lightbulbs.

I have added some photos that we think is good inspirational material and would be good as a background to this website, but we want the site to look modern but not conventional. We would like something that makes our company look quirky not corporate.

Thats it

Target Market(s)

Our product is being stocked by big name online retailers in the UK, the page will get link through hits from our app. Our target market is gadget freaks of all ages.

Industry/Entity Type

It Company

Requirements
Must have
• We are going to need a help page, text to be uploaded next few days.

We need a contact page.

design my work on iOS and Android as most people will access page through their handset or tablet.
Should not have
• We do not want anything too corporate.

```html
<!DOCTYPE html>
<html lang="en">
<head>
<meta charset="utf-8">
<title>brightquokka – App Controlled LED Lightbulbs</title>
<link href="https://fonts.googleapis.com/css2?family=Open+Sans:ital,wght@0,300;0,400;0,600;0,700;1,400&display=swap" rel="stylesheet">
<style>
:root{
  --green:#3aaa4a;
  --green-dark:#2f9a3f;
  --ink:#2b2b2b;
  --muted:#555;
  --paper:#ebebeb;
  --strip:#1c1c1c;
  --footer:#232323;
  --footer-base:#121212;
  --footer-text:#8a8a8a;
}
*{box-sizing:border-box;margin:0;padding:0}
html,body{width:736px;height:1200px;overflow:hidden}
body{position:relative;font-family:"Open Sans",Arial,sans-serif;color:var(--ink);background:#fff}
.abs{position:absolute}

/* top bar */
.topbar{left:0;top:0;width:736px;height:32px;background:var(--green);color:#fff;font-size:9.5px;display:flex;justify-content:flex-end;align-items:center;gap:14px;padding-right:19px}

/* sidebar */
.sidebar{left:0;top:32px;width:130px;height:375px;background:#fff}
.logo-mark{left:22px;top:50px;width:86px;height:120px;display:flex;align-items:center;justify-content:center}
.logo-name{left:0;top:170px;width:130px;text-align:center;font-size:8px;font-weight:700;color:var(--green);letter-spacing:.2px}
.nav{left:22px;top:183px;width:86px;list-style:none}
.nav li{height:23px;line-height:23px;font-size:8px;color:#444;border-bottom:1px solid #ddd;text-transform:uppercase}
.nav li:last-child{border-bottom:none}
.nav li.active{color:var(--green)}

/* hero */
.hero{left:130px;top:32px;width:606px;height:300px;background:radial-gradient(ellipse at 50% 30%,#f2f2f2 0%,#cfcfcf 55%,#8e8e8e 100%)}
.strip{left:130px;top:332px;width:606px;height:75px;background:var(--strip)}
.thumb{top:344px;width:86px;height:52px}
.t1{left:249px;background:linear-gradient(135deg,#e8e8e8,#9a9a9a)}
.t2{left:342px;background:linear-gradient(135deg,#7a3a22,#e6d2c0 55%,#4a2a1c)}
.t3{left:436px;background:linear-gradient(135deg,#3a2a1a,#e0a030 50%,#6a4a20)}
.t4{left:529px;background:linear-gradient(135deg,#2a1a10,#c07030 50%,#3a2416)}
.arrow{top:358px;width:14px;height:24px}

/* welcome */
.welcome{left:0;top:407px;width:736px;height:219px;background:var(--paper);text-align:center}
.welcome h1{position:absolute;left:0;top:38px;width:736px;font-size:18px;font-weight:400;color:#222}
.welcome h2{position:absolute;left:0;top:60px;width:736px;font-size:12px;font-weight:400;color:#333}
.welcome p{position:absolute;left:96px;top:90px;width:544px;font-size:7.6px;line-height:9.7px;color:#444}
.notch{left:360px;top:626px;width:16px;height:9px;z-index:2}

/* products */
.products{left:0;top:626px;width:736px;height:448px;background:radial-gradient(ellipse at 20% 80%,#c9a98a 0%,transparent 45%),radial-gradient(ellipse at 85% 60%,#d8c4a8 0%,transparent 40%),linear-gradient(160deg,#4a2c22 0%,#7a5040 35%,#a87a5c 60%,#5a3a2a 100%)}
.card{top:662px;width:168px;height:215px;background:rgba(255,255,255,.85)}
.card .photo{height:113px}
.card h3{margin-top:12px;text-align:center;font-size:10.5px;font-weight:400;color:#333}
.card p{margin:4px auto 0;width:140px;text-align:center;font-size:7.5px;line-height:9.7px;color:#444}
.card .btn{position:absolute;left:0;bottom:0;width:168px;height:22px;line-height:22px;background:var(--green);color:#fff;text-align:center;font-size:8px;font-style:italic}
.c1{left:101px}.c2{left:284px}.c3{left:467px}
.c1 .photo{background:linear-gradient(120deg,#f6e6cc,#c8a070 60%,#3a2a22)}
.c2 .photo{background:radial-gradient(circle at 50% 50%,#ffffff 40%,#e6e6e6)}
.c3 .photo{background:linear-gradient(135deg,#2a3440,#6a7480 50%,#1e242c)}
.other-title{left:101px;top:897px;font-size:13px;font-weight:400;color:#fff}
.other{left:101px;top:915px;width:534px;height:135px;background:rgba(255,255,255,.82)}
.item{top:935px;width:116px}
.item .photo{height:77px}
.item .name{margin-top:6px;text-align:center;font-size:8.5px;color:#222}
.item .sub{margin-top:2px;text-align:center;font-size:7.5px;font-style:italic;color:var(--green)}
.i1{left:121px}.i2{left:247px}.i3{left:373px}.i4{left:498px}
.i1 .photo{background:linear-gradient(135deg,#3a2a1a,#e0a030 50%,#5a3a1a)}
.i2 .photo{background:linear-gradient(135deg,#7a3a22,#ecdccc 55%,#5a2a1c)}
.i3 .photo{background:linear-gradient(135deg,#f0f0f0,#b8b8b8)}
.i4 .photo{background:radial-gradient(circle at 55% 50%,#e8c890 0%,#6a4a30 45%,#1e1610 100%)}

/* footer */
.footer{left:0;top:1074px;width:736px;height:99px;background:var(--footer)}
.f-head{font-size:9px;font-weight:600;color:var(--green)}
.f-text{font-size:6.5px;line-height:8.2px;color:var(--footer-text);text-transform:uppercase}
.f-brand{left:80px;top:1094px}
.f-support{left:300px;top:1093px}
.f-shop{left:410px;top:1093px}
.f-follow{left:539px;top:1094px}
.divider{top:1094px;width:1px;height:68px;background:#3a3a3a}
.social{top:1092px;width:15px;height:15px;border-radius:50%;background:#888}
.base{left:0;top:1173px;width:736px;height:27px;background:var(--footer-base);font-size:6.5px;color:#666;text-align:right;line-height:27px;padding-right:80px}
</style>
</head>
<body>

<header class="abs topbar">
  <span>E-Mail: info@brightquokka.net</span>
  <span>Phone: +100 555 0142</span>
</header>

<aside class="abs sidebar"></aside>
<div class="abs logo-mark">
  <svg width="14" height="14" viewBox="0 0 14 14" aria-hidden="true"><circle cx="7" cy="7" r="7" fill="#3aaa4a"/></svg>
</div>
<div class="abs logo-name">BRIGHTQUOKKA</div>
<ul class="abs nav" style="top:210px">
  <li class="active">Home</li>
  <li>About us</li>
  <li>Services</li>
  <li>Gallery</li>
  <li>Blog</li>
  <li>Testimonials</li>
  <li>Contact us</li>
</ul>

<section class="abs hero" role="img" aria-label="Smart LED bulb beside a smartphone showing a colour wheel app"></section>
<div class="abs strip"></div>
<svg class="abs arrow" style="left:208px" viewBox="0 0 14 24" aria-hidden="true"><path d="M11 3 3 12l8 9" fill="none" stroke="#bbb" stroke-width="3"/></svg>
<div class="abs thumb t1" role="img" aria-label="Bulb and phone thumbnail"></div>
<div class="abs thumb t2" role="img" aria-label="Ceramic seal lamp thumbnail"></div>
<div class="abs thumb t3" role="img" aria-label="Row of toy figurine lamps thumbnail"></div>
<div class="abs thumb t4" role="img" aria-label="Shop full of hanging lamps thumbnail"></div>
<svg class="abs arrow" style="left:643px" viewBox="0 0 14 24" aria-hidden="true"><path d="M3 3l8 9-8 9" fill="none" stroke="#bbb" stroke-width="3"/></svg>

<section class="abs welcome">
  <h1>Welcome to brightquokka</h1>
  <h2>is a leader in World’s affordable app controlled LED lightbulbs industry</h2>
  <p>Duis semper, nisl accumsan placerat porta, arcu neque pulvinar sapien, ut elementum elit urna in arcu. Sed ut sodales risus. Suspendisse pretium vitae neque at fermentum. Aliquam elementum auctor eros in dapibus. Fusce nulla neque, fringilla quis interdum sed, malesuada in tortor. Aenean sit amet dictum massa, et sagittis nibh. Morbi iaculis, elit sed dictum tristique, erat ante elementum nulla, quis consectetur sem justo id ante. Fusce lorem tortor, auctor eget hendrerit vel, egestas eget leo.Our strength lies in the experience behind designing and manufacturing kitchens, interior doors, entertainment units and office work areas. Our state of the art equipment, locations and strong partnerships with suppliers allow us to manufacture high quality products and to supply any customer. Our clients range from residential customers wanting a designer kitchen to building centers and contractors to whom we supply stock cabinets and doors.</p>
</section>

<section class="abs products" role="img" aria-label="Blurred warm interior with a table lamp, used as background"></section>
<svg class="abs notch" viewBox="0 0 16 9" aria-hidden="true"><path d="M0 0h16L8 9z" fill="#ebebeb"/></svg>

<article class="abs card c1">
  <div class="photo" role="img" aria-label="Glowing bulb next to a hand holding a phone with a dimmer app"></div>
  <h3>APP CONTROLLED</h3>
  <p>Seems like these days we are able to control almost everything from our smartphones. Say hello to the world´s first networked dimmable light bulb!</p>
  <div class="btn">Know more</div>
</article>
<article class="abs card c2">
  <div class="photo" role="img" aria-label="LED bulb and phone with colour wheel app"></div>
  <h3>APP CONTROLLED</h3>
  <p>Seems like these days we are able to control almost everything from our smartphones. Say hello to the world´s first networked dimmable light bulb!</p>
  <div class="btn">Know more</div>
</article>
<article class="abs card c3">
  <div class="photo" role="img" aria-label="Pendant lights hanging in a stairwell"></div>
  <h3>APP CONTROLLED</h3>
  <p>Seems like these days we are able to control almost everything from our smartphones. Say hello to the world´s first networked dimmable light bulb!</p>
  <div class="btn">Know more</div>
</article>

<div class="abs other-title">OTHER PRODUCTS</div>
<div class="abs other"></div>
<div class="abs item i1"><div class="photo" role="img" aria-label="Toy figurine lamps in a row"></div><div class="name">Neque porro quisquam</div><div class="sub">dolorem ipsum</div></div>
<div class="abs item i2"><div class="photo" role="img" aria-label="Ceramic seal shaped lamp"></div><div class="name">Neque porro quisquam</div><div class="sub">dolorem ipsum</div></div>
<div class="abs item i3"><div class="photo" role="img" aria-label="White LED bulbs and spotlight"></div><div class="name">Neque porro quisquam</div><div class="sub">dolorem ipsum</div></div>
<div class="abs item i4"><div class="photo" role="img" aria-label="Crystal ceiling chandelier"></div><div class="name">Neque porro quisquam</div><div class="sub">dolorem ipsum</div></div>

<footer class="abs footer"></footer>
<div class="abs f-brand">
  <div class="f-head">BRIGHTQUOKKA</div>
  <div class="f-text" style="margin-top:4px">Sample address<br>Brookvale, Northshire, K2P 4Q7</div>
  <div class="f-text" style="margin-top:5px">E-mail: <span style="font-size:8px;text-transform:none">info@brightquokka.net</span><br>Phone: <span style="font-size:10px">+100 555 0142</span></div>
</div>
<div class="abs divider" style="left:280px"></div>
<div class="abs f-support">
  <div class="f-head">SUPPORT</div>
  <div class="f-text" style="margin-top:6px">Download app<br>Updates<br>Shipping &amp; delivery<br>Forum<br>Developers</div>
</div>
<div class="abs divider" style="left:386px"></div>
<div class="abs f-shop">
  <div class="f-head">SHOP</div>
  <div class="f-text" style="margin-top:6px">Lighting 101<br>Edison bulbs<br>Bayonet bulbs<br>Downlights<br>Our app</div>
</div>
<div class="abs divider" style="left:498px"></div>
<div class="abs f-follow f-head">FOLLOW US</div>
<div class="abs social" style="left:606px"></div>
<div class="abs social" style="left:624px"></div>
<div class="abs social" style="left:642px"></div>
<div class="abs base">© COPYRIGHT 2014 . ALL RIGHTS RESERVED TO BRIGHTQUOKKA.NET</div>

</body>
</html>
```